Card design for orthopaedic surgeons working as The Brightwater Joint Centre

Business cards, letterhead

Colors

Designer to choose colors to be used in the design.

Requirements
Must have
• Late addition.
• Cards letterhead must have logos of
• Crestmoor Lindell College of Surgeons
• Varenwood Bone Health Association
Nice to have
• Back of card to have space for appointment time to be added by hand and some blank space for writing incidental other notes.

```html
<!DOCTYPE html>
<html lang="en">
<head>
<meta charset="utf-8">
<title>The Brightwater Joint Centre — Letterhead</title>
<link rel="stylesheet" href="https://fonts.googleapis.com/css2?family=Open+Sans:wght@400;500;600&family=Roboto:wght@400&display=swap">
<style>
  :root {
    --backdrop: #e4e5e7;
    --paper: #ffffff;
    --ink: #3f4347;
    --brand-blue: #2f8fce;
    --rule: #4a5a6a;
    --footer-ink: #3b5570;
    --sign-tone: #e9eaec;
  }
  * { margin: 0; padding: 0; box-sizing: border-box; }
  html, body {
    width: 1040px; height: 1200px; overflow: hidden;
    background: var(--backdrop);
  }
  .letterhead {
    position: absolute; left: 77px; top: 30px;
    width: 886px; height: 1140px;
    background: var(--paper);
    box-shadow: 0 2px 10px rgba(0,0,0,0.12);
    font-family: "Open Sans", sans-serif;
    color: var(--ink);
  }
  .brand-name {
    position: absolute; left: 0; right: 0; top: 53px;
    text-align: center;
    font-family: "Open Sans", sans-serif;
    font-weight: 500; font-size: 20px; letter-spacing: -0.2px;
    color: var(--brand-blue);
  }
  .rule {
    position: absolute; left: 72px; width: 741px; height: 1px;
    background: var(--rule);
  }
  .rule--top { top: 86px; }
  .rule--bottom { top: 1102px; }
  .letter-date {
    position: absolute; left: 98px; top: 316px;
    font-size: 14.5px;
  }
  .letter-body {
    position: absolute; left: 98px; top: 388px; width: 700px;
    font-size: 14.5px; line-height: 31.4px;
  }
  .letter-body p { margin-bottom: 4px; white-space: nowrap; }
  .signature {
    position: absolute; left: 611px; top: 808px;
    width: 176px; height: 50px;
    background: var(--sign-tone); border-radius: 4px;
  }
  .signer {
    position: absolute; left: 616px; top: 856px;
    font-size: 14.5px; line-height: 18px;
  }
  .footer-address {
    position: absolute; left: 0; right: 0; top: 1081px;
    text-align: center;
    font-family: "Roboto", sans-serif; font-size: 13px;
    color: var(--footer-ink);
  }
  .footer-contacts {
    position: absolute; left: 0; right: 0; top: 1107px;
    display: flex; justify-content: center; gap: 16px;
    font-family: "Roboto", sans-serif; font-size: 13px;
    color: var(--footer-ink);
  }
  .contact { display: flex; align-items: center; gap: 6px; }
  .contact svg { width: 10px; height: 10px; fill: var(--brand-blue); }
</style>
</head>
<body>
  <main class="letterhead">
    <header>
      <div class="brand-name">The Brightwater Joint Centre</div>
      <div class="rule rule--top"></div>
    </header>

    <div class="letter-date">Date, 10 September, 2020</div>

    <section class="letter-body">
      <p>This is a sample letter that has been placed to demonstrate typing remat (Your Company). letterhead<br>
      design. When positioned properly, it will serve to work in harmony with all other elements letterhead.<br>
      This letterhead design is meant to project an image</p>
      <p>This letterhead design is meant project an image of professionalism reliability. By using simple aligen<br>
      we have created a very spacious feeling. The simplicity suggest &nbsp;rengththe spaciousnes contributes h<br>
      aesthetics the layout. These basic qualities along with the (Your Company)</p>
      <p>look and helps reinforce the (Your Company) brand. letterhead design is meant to project an image p<br>
      design. When positioned properly, it will serve to work in harmony all the other elements letterhead.<br>
      sionalism and reliability.</p>
      <p>This letterhead design is based on the (Form of your logo) form (Your Company) logo. Each stationery<br>
      we have created a very spacious feeling. The simplicity suggests strength the spaciousnes contribute<br>
      part of the (Form of your logo).</p>
    </section>

    <div class="signature" role="img" aria-label="Handwritten signature of Daniel Hartwell"></div>
    <div class="signer">Daniel Hartwell<br>Manager</div>

    <footer>
      <div class="footer-address">Your address, city, state, ZIP 0000</div>
      <div class="rule rule--bottom"></div>
      <div class="footer-contacts">
        <span class="contact">
          <svg viewBox="0 0 10 10" aria-hidden="true"><path d="M2 0.5l2 2-1 1.2c.6 1.3 1.6 2.3 2.9 2.9l1.2-1 2 2-1.3 1.6C4.4 9.1.9 5.6.4 1.8z"/></svg>
          123-456-2100
        </span>
        <span class="contact">
          <svg viewBox="0 0 10 10" aria-hidden="true"><path d="M0 2h10v6H0z M0.8 2.6L5 5.6 9.2 2.6" stroke="#fff" stroke-width="0.8"/></svg>
          youremail@mailbox.com
        </span>
        <span class="contact">
          <svg viewBox="0 0 10 10" aria-hidden="true"><circle cx="5" cy="5" r="5"/><path d="M0 5h10M5 0c-2.5 2.8-2.5 7.2 0 10M5 0c2.5 2.8 2.5 7.2 0 10" stroke="#fff" stroke-width="0.7" fill="none"/></svg>
          www.yourwebsite.com
        </span>
      </div>
    </footer>
  </main>
</body>
</html>
```